Heritage Hollow Business Cards

Require a business card design. <br/><br/>Needs to include logo (either round or long version) plus these details:<br/>Maya Torvell<br/>Heritage Hollow<br/>maya@kelvadtrading.com.au<br/>02 6481 7395<br/>PO Box Glenwarra NSW 2791<br/>www.heritagehollow.com.au<br/><br/>I need in an editable format so that I can create for multiple staff members. <br/><br/>

Target Market(s)

We are an online store selling renovation products to home owners are builders. Looking for a classic classy design.

Industry/Entity Type

Home And Garden

Contact Information for Business Card

Maya Torvell
Heritage Hollow
maya@kelvadtrading.com.au
02 6481 7395
PO Box Glenwarra NSW 2791
www.heritagehollow.com.au

Colors

Designer to choose colors to be used in the design.

Requirements
Must have
• Must include Logo.

```html
<!DOCTYPE html>
<html lang="en">
<head>
<meta charset="utf-8">
<title>Heritage Hollow Business Cards</title>
<link rel="stylesheet" href="https://fonts.googleapis.com/css2?family=Lora:wght@400;600;700&display=swap">
<style>
  :root {
    --page-bg: #1a1b1d;
    --card-bg: #26282b;
    --card-edge: #303236;
    --foil: #d8d9db;
    --foil-soft: #a9abaf;
    --emboss: #4a4c50;
    --line: #0f1011;
  }
  * { margin: 0; padding: 0; box-sizing: border-box; }
  html, body {
    width: 1200px; height: 800px; overflow: hidden;
    background: var(--page-bg);
    font-family: "Lora", Georgia, serif;
  }
  .canvas { position: relative; width: 1200px; height: 800px; }
  .card {
    position: absolute; width: 540px; height: 320px;
    background: var(--card-bg);
    border: 1px solid var(--card-edge);
    border-radius: 18px;
    overflow: hidden;
  }
  .card--back { left: 60px; top: 80px; }
  .card--front { left: 600px; top: 400px; }

  /* Back */
  .back-mark {
    position: absolute; left: 50%; top: 50%;
    transform: translate(-50%, -50%);
    display: flex; align-items: center; gap: 12px;
  }
  .back-mark__circle {
    width: 26px; height: 26px; border-radius: 50%;
    border: 2px solid var(--emboss);
  }
  .back-mark__name {
    font-size: 30px; font-weight: 400; color: var(--emboss);
  }

  /* Front */
  .front-ring {
    position: absolute; right: -90px; top: -40px;
    width: 300px; height: 300px; border-radius: 50%;
    border: 2px solid var(--line);
  }
  .front-brand {
    position: absolute; left: 34px; top: 44px;
    display: flex; align-items: center; gap: 12px;
  }
  .front-brand__circle {
    width: 30px; height: 30px; border-radius: 50%;
    border: 2px solid var(--foil);
  }
  .front-brand__name {
    font-size: 34px; font-weight: 600; color: var(--foil);
  }
  .person { position: absolute; left: 34px; top: 150px; }
  .person__name {
    font-size: 22px; font-weight: 700; color: var(--foil); line-height: 1.2;
  }
  .person__role {
    font-size: 13px; color: var(--foil-soft); margin-top: 2px;
  }
  .contact {
    position: absolute; left: 34px; top: 222px;
    font-size: 12.5px; line-height: 1.6; color: var(--foil-soft);
  }
  .contact strong { color: var(--foil); font-weight: 700; font-style: italic; }
</style>
</head>
<body>
<main class="canvas">
  <section class="card card--back" aria-label="Business card back">
    <div class="back-mark">
      <span class="back-mark__circle"></span>
      <span class="back-mark__name">Heritage Hollow</span>
    </div>
  </section>

  <section class="card card--front" aria-label="Business card front">
    <div class="front-ring"></div>
    <div class="front-brand">
      <span class="front-brand__circle"></span>
      <span class="front-brand__name">Heritage Hollow</span>
    </div>
    <div class="person">
      <p class="person__name">Maya Torvell</p>
      <p class="person__role">Managing Director</p>
    </div>
    <div class="contact">
      <p><strong>Phone</strong>: 02 6481 7395 | <strong>Email</strong>: maya@kelvadtrading.com.au</p>
      <p>PO Box Glenwarra NSW 2791</p>
      <p>www.<strong>heritagehollow</strong>.com.au</p>
    </div>
  </section>
</main>
</body>
</html>
```